Wedding Ceremony Equipment Hire Business Card

I need a business card design for a new business I created called Vowline Rentals. We hire out Wedding Ceremony equipment and decorations mainly for beach and garden wedding ceremonies that include delivery, set up and dismantle. We do offer DIY Chair Hire as well.
I'd like to have a similar design and colours to our website:
www.vowlinerentals.com.au
If possible would like the front to incorporate our information and logo and the back to have two faded example pictures of our wedding ceremonies.
I have attached two photos and our logo. Please let me know if you need a better pic of our logo though.

Target Market(s)

Newly engaged couples, aged 25 and upwards

Industry/Entity Type

Wedding

Contact Information for Business Card

Vowline Rentals
Mira Holt
0412 908 146
hello@vowlinerentals.com.au
www.vowlinesocial.com/VowlineRentals

```html
<!DOCTYPE html>
<html lang="en">
<head>
<meta charset="utf-8">
<title>Vowline Rentals – Business Card</title>
<link rel="stylesheet" href="https://fonts.googleapis.com/css2?family=Cormorant+Garamond:ital,wght@0,500;1,500&display=swap">
<style>
  :root {
    --backdrop: #e9e6e1;
    --card-dark: #262626;
    --mint: #84d8b5;
    --mint-soft: #9fe3c6;
    --ink: #1d1d1d;
    --paper: #f4f4f4;
    --ornament: rgba(200, 200, 200, 0.35);
    --serif: "Cormorant Garamond", Georgia, serif;
  }
  * { box-sizing: border-box; margin: 0; padding: 0; }
  html, body {
    width: 1200px; height: 750px; overflow: hidden;
    background: var(--backdrop);
    font-family: var(--serif);
  }
  .canvas { position: relative; width: 1200px; height: 750px; }

  .card {
    position: absolute;
    width: 528px; height: 323px;
    background: var(--card-dark);
    overflow: hidden;
    box-shadow: 0 2px 8px rgba(0,0,0,0.25);
  }
  .card--front { left: 91px; top: 44px; }
  .card--back { left: 565px; top: 389px; }

  /* Front */
  .front-band {
    position: absolute; left: 0; top: 112px;
    width: 100%; height: 97px;
    background: var(--mint);
  }
  .front-ornament {
    position: absolute; left: 0; top: 0;
    width: 280px; height: 323px;
    background: radial-gradient(ellipse at 40% 45%, var(--ornament), rgba(200,200,200,0) 70%);
  }
  .brand-name {
    position: absolute; left: 172px; top: 128px;
    width: 190px;
    font-family: var(--serif);
    font-weight: 500;
    font-size: 38px;
    line-height: 34px;
    color: var(--ink);
    text-align: center;
  }
  .contact {
    position: absolute; left: 341px; top: 214px;
    width: 174px;
    text-align: center;
    font-style: italic;
  }
  .contact__name {
    font-size: 22px; line-height: 30px;
    color: var(--mint);
    border-bottom: 2px solid var(--mint);
    padding-bottom: 3px;
    margin-bottom: 4px;
  }
  .contact__line {
    font-size: 10.5px; line-height: 12.5px;
    color: var(--mint-soft);
    white-space: nowrap;
  }
  .contact__line--phone { color: var(--paper); font-size: 12px; line-height: 14px; }

  /* Back */
  .back-rule {
    position: absolute; left: 0; width: 100%; height: 4px;
    background: var(--mint);
  }
  .back-rule--top { top: 55px; }
  .back-rule--bottom { top: 276px; }
  .ceremony-photo {
    position: absolute; top: 59px; height: 217px;
  }
  .ceremony-photo--beach {
    left: 0; width: 264px;
    background: linear-gradient(180deg, #1f4fd8 0%, #3f78e6 38%, #c9883f 55%, #b8743a 100%);
  }
  .ceremony-photo--garden {
    left: 266px; width: 262px;
    background: linear-gradient(180deg, #5a9de8 0%, #9cc3e8 35%, #3f7d34 55%, #3a8a2c 100%);
  }
  .back-brand {
    position: absolute; right: 14px; bottom: 8px;
    font-family: var(--serif);
    font-weight: 500;
    font-size: 17px;
    color: var(--paper);
  }
</style>
</head>
<body>
<main class="canvas">
  <section class="card card--front" aria-label="Business card front">
    <div class="front-ornament" role="img" aria-label="Soft grey flourish ornament"></div>
    <div class="front-band"></div>
    <h1 class="brand-name">Vowline Rentals</h1>
    <div class="contact">
      <p class="contact__name">Mira Holt</p>
      <p class="contact__line contact__line--phone">Call us: 0412 908 146</p>
      <p class="contact__line">hello@vowlinerentals.com.au</p>
      <p class="contact__line">www.vowlinerentals.com.au</p>
      <p class="contact__line">www.vowlinesocial.com/VowlineRentals</p>
    </div>
  </section>

  <section class="card card--back" aria-label="Business card back">
    <div class="back-rule back-rule--top"></div>
    <div class="ceremony-photo ceremony-photo--beach" role="img" aria-label="Beach wedding ceremony with white chairs lining a sandy aisle"></div>
    <div class="ceremony-photo ceremony-photo--garden" role="img" aria-label="Garden wedding ceremony with white chairs and aisle runner beside a harbour"></div>
    <div class="back-rule back-rule--bottom"></div>
    <p class="back-brand">Vowline Rentals</p>
  </section>
</main>
</body>
</html>
```